RTavenor Business Cards & Letterhead

I have a logo but need a design for some new business cards. We are a Design-Build Firm that specializes in the design and construction of commercial projects.
the cards need to be professional. no cartoon stuff.
i would like to have the cards in AI format so I can update the card as needed. Logo is provided.
Our Address is: 4187 Marlowe Ct. Alder Falls, New Fairhaven 27614

```html
<!DOCTYPE html>
<html lang="en">
<head>
<meta charset="utf-8">
<title>RTavenor Business Card</title>
<link href="https://fonts.googleapis.com/css2?family=Open+Sans:wght@400;600;800&display=swap" rel="stylesheet">
<style>
  :root {
    --bg: #2a2e35;
    --card-white: #fbfbf4;
    --navy: #163a6b;
    --blue: #0f5a9c;
    --blue-bright: #1a78bd;
    --ink: #1e1f22;
    --brand-grey: #3b3e44;
    --white: #ffffff;
  }
  * { box-sizing: border-box; margin: 0; padding: 0; }
  html, body { width: 1200px; height: 780px; overflow: hidden; }
  body {
    background: var(--bg);
    font-family: "Open Sans", Arial, sans-serif;
    position: relative;
  }
  .card {
    position: absolute;
    top: 235px;
    width: 540px;
    height: 309px;
    border-radius: 22px;
    overflow: hidden;
  }
  /* Front */
  .card-front { left: 40px; background: var(--card-white); }
  .brand-feature {
    position: absolute;
    left: 18px; top: 18px;
    width: 220px; height: 215px;
    border-radius: 30px;
    background: linear-gradient(135deg, var(--navy) 0%, var(--blue) 55%, var(--blue-bright) 100%);
  }
  .wordmark {
    position: absolute;
    right: 26px; top: 42px;
    display: flex; align-items: center; gap: 8px;
    font-weight: 800;
    font-size: 36px;
    letter-spacing: 0.5px;
    color: var(--brand-grey);
  }
  .wordmark-square {
    width: 22px; height: 22px;
    background: var(--blue);
  }
  .name-band {
    position: absolute;
    left: 238px; right: 0; top: 112px;
    height: 40px;
    background: linear-gradient(90deg, rgba(22,58,107,0) 0%, #3d5b8c 30%, var(--navy) 65%);
    display: flex; align-items: center; justify-content: flex-end;
    padding-right: 26px;
  }
  .person-name {
    color: var(--white);
    font-weight: 600;
    font-size: 24px;
    letter-spacing: 0.5px;
  }
  .person-title {
    position: absolute;
    right: 26px; top: 155px;
    color: var(--navy);
    font-size: 16px;
  }
  .contact {
    position: absolute;
    right: 26px; top: 188px;
    text-align: right;
    color: var(--ink);
    font-size: 14.5px;
    line-height: 20px;
  }
  .address { margin-bottom: 6px; }
  .contact-line {
    display: flex; align-items: center; justify-content: flex-end; gap: 6px;
  }
  .contact-icon { width: 14px; height: 14px; flex: none; }
  /* Back */
  .card-back {
    left: 620px;
    background: linear-gradient(150deg, #0d335c 0%, var(--navy) 40%, var(--blue) 100%);
  }
  .back-pattern-area {
    position: absolute; inset: 0;
    background: linear-gradient(135deg, rgba(0,0,0,0.12) 0%, rgba(255,255,255,0) 45%, rgba(40,130,210,0.25) 100%);
  }
  .back-wordmark {
    position: absolute;
    right: 50px; bottom: 60px;
    display: flex; align-items: center; gap: 10px;
    font-weight: 800;
    font-size: 40px;
    color: var(--white);
    letter-spacing: 0.5px;
  }
  .back-wordmark .wordmark-square { background: var(--white); width: 24px; height: 24px; }
</style>
</head>
<body>
  <section class="card card-front">
    <div class="brand-feature" role="img" aria-label="Large company brand symbol in blue"></div>
    <div class="wordmark"><span class="wordmark-square"></span>RTAVENOR</div>
    <div class="name-band"><span class="person-name">MARCUS TAVENOR</span></div>
    <div class="person-title">Founder/President</div>
    <div class="contact">
      <p class="address">4187 Marlowe Ct. Alder Falls,<br>New Fairhaven 27614</p>
      <p class="contact-line">(555) 612-0148
        <svg class="contact-icon" viewBox="0 0 14 14"><circle cx="7" cy="7" r="7" fill="#0f5a9c"/><path d="M4.5 3.5l1.5 0 .6 2-1 .8a5 5 0 0 0 2.1 2.1l.8-1 2 .6 0 1.5c-3.5.3-6.3-2.5-6-6z" fill="#fff"/></svg>
      </p>
      <p class="contact-line">www.rtavenor.com
        <svg class="contact-icon" viewBox="0 0 14 14"><circle cx="7" cy="7" r="7" fill="#0f5a9c"/><circle cx="7" cy="7" r="4.5" fill="none" stroke="#fff" stroke-width="1"/><ellipse cx="7" cy="7" rx="2" ry="4.5" fill="none" stroke="#fff" stroke-width="1"/><line x1="2.5" y1="7" x2="11.5" y2="7" stroke="#fff" stroke-width="1"/></svg>
      </p>
      <p class="contact-line">MRT@RTavenor.com
        <svg class="contact-icon" viewBox="0 0 14 14"><rect width="14" height="14" rx="2" fill="#0f5a9c"/><rect x="2.5" y="4" width="9" height="6.5" fill="none" stroke="#fff" stroke-width="1"/><path d="M2.5 4l4.5 3.5 4.5-3.5" fill="none" stroke="#fff" stroke-width="1"/></svg>
      </p>
    </div>
  </section>

  <section class="card card-back">
    <div class="back-pattern-area" role="img" aria-label="Repeating brand pattern in blue tones"></div>
    <div class="back-wordmark"><span class="wordmark-square"></span>RTAVENOR</div>
  </section>
</body>
</html>
```